Mira Bloom Fitness Coaching Project

I am a personal trainer based in London. My services include one-on-one PT sessions, bootcamps.
I would like the design to be minimalistic. With light colours: white, pink, purple.
I specialise in weight loss, flexibility, mobility.

Tessa Brogan
Personal Trainer
Email: tessa.brogan@quellmail.com
tel: 07700218493
Instagram: Mira Bloom

Target Market(s)

adults, mostly females (age 18-50).

Industry/Entity Type

Fitness

Contact Information for Business Card

Tessa Brogan
Personal Trainer
tel: 07700218493
Instagram: Mira Bloom

Font styles to use
Serif

Colors
eea4c8
fbd4d5
fdf9cf
cfeae6
cee9f5

Requirements
Nice to have
• minimalistic style
• easy to read and remember

```html
<!DOCTYPE html>
<html lang="en">
<head>
<meta charset="utf-8">
<title>Tessa Brogan – Personal Trainer Business Card</title>
<link rel="stylesheet" href="https://fonts.googleapis.com/css2?family=Jost:wght@400;500;700;800&display=swap">
<style>
  :root {
    --page-bg: #e6e6e8;
    --card-bg: #ffffff;
    --accent-pink: #e455d6;
    --text-grey: #5a5a5e;
    --text-dark: #4a4a4e;
    --photo-rose: #f3b3aa;
    --photo-coral: #e98479;
  }

  * { margin: 0; padding: 0; box-sizing: border-box; }

  html, body {
    width: 1200px;
    height: 900px;
    overflow: hidden;
    background: var(--page-bg);
    font-family: "Jost", sans-serif;
  }

  .canvas {
    width: 1200px;
    height: 900px;
    display: flex;
    align-items: center;
    justify-content: center;
  }

  .business-card {
    position: relative;
    width: 900px;
    height: 560px;
    background: var(--card-bg);
    border-radius: 30px;
    overflow: hidden;
    box-shadow: 0 14px 40px rgba(0, 0, 0, 0.18);
  }

  .accent-stripe {
    position: absolute;
    left: 0;
    top: 0;
    width: 24px;
    height: 100%;
    background: var(--accent-pink);
  }

  .hero-photo {
    position: absolute;
    right: 0;
    top: 0;
    width: 62%;
    height: 100%;
    background: linear-gradient(to right,
      rgba(243, 179, 170, 0) 0%,
      var(--photo-rose) 40%,
      var(--photo-coral) 100%);
  }

  .card-details {
    position: absolute;
    left: 78px;
    top: 268px;
    color: var(--text-grey);
  }

  .trainer-name {
    font-size: 40px;
    font-weight: 800;
    letter-spacing: 1px;
    color: var(--accent-pink);
    text-transform: uppercase;
    line-height: 1;
  }

  .trainer-role {
    margin-top: 8px;
    font-size: 25px;
    font-weight: 400;
    color: var(--text-grey);
  }

  .contact-list {
    list-style: none;
    margin-top: 20px;
  }

  .contact-item {
    display: flex;
    align-items: center;
    gap: 14px;
    font-size: 25px;
    line-height: 34px;
    color: var(--text-grey);
  }

  .contact-icon {
    width: 20px;
    height: 20px;
    flex: none;
  }

  .social-mark {
    width: 18px;
    height: 18px;
    flex: none;
    margin: 0 1px;
    background: var(--accent-pink);
    border-radius: 3px;
  }

  .services-line {
    margin-top: 22px;
    font-size: 24px;
    font-weight: 700;
    color: var(--text-dark);
  }
</style>
</head>
<body>
  <main class="canvas">
    <article class="business-card">
      <div class="accent-stripe"></div>
      <div class="hero-photo" role="img" aria-label="Photo of the trainer doing a handstand split outdoors"></div>

      <section class="card-details">
        <h1 class="trainer-name">Tessa Brogan</h1>
        <p class="trainer-role">Personal Trainer</p>

        <ul class="contact-list">
          <li class="contact-item">
            <svg class="contact-icon" viewBox="0 0 24 24" aria-hidden="true">
              <path fill="var(--accent-pink)" d="M6.6 10.8a15.2 15.2 0 0 0 6.6 6.6l2.2-2.2c.3-.3.7-.4 1-.2 1.1.4 2.3.6 3.6.6.6 0 1 .4 1 1V20c0 .6-.4 1-1 1A17 17 0 0 1 3 4c0-.6.4-1 1-1h3.5c.6 0 1 .4 1 1 0 1.3.2 2.5.6 3.6.1.3 0 .7-.2 1z"/>
            </svg>
            <span>07700218493</span>
          </li>
          <li class="contact-item">
            <svg class="contact-icon" viewBox="0 0 24 24" aria-hidden="true">
              <rect x="2" y="5" width="20" height="14" rx="2" fill="var(--accent-pink)"/>
              <path d="M3 6.5l9 6.5 9-6.5" fill="none" stroke="#fff" stroke-width="1.8"/>
            </svg>
            <span>tessa.brogan@quellmail.com</span>
          </li>
          <li class="contact-item">
            <span class="social-mark" aria-hidden="true"></span>
            <span>Mira Bloom</span>
          </li>
        </ul>

        <p class="services-line">PT sessions, bootcamps.</p>
      </section>
    </article>
  </main>
</body>
</html>
```